Clinic for cellulit and fat removal

Name of clinic :
Lirava
- Body & Health (this has to be written on the site.)
I need CMS for me to be able to make changes myself.
A webpage for woman searching for a solution to remove fat and cellulit.
The owner is a brazilian woman in Denmark, and want her sense of aestetic shines thru the website.
There needs to be a slide show on the landing page showing big sliding pictures, of the clinic and and the treatments.
The Cryolipolysis, is a treatment freezing fat and cellulit, and this treatment will be the Attraction of the clinic.
Needs These pages in a horisontal fasion. (written in Danish)
Lirava
Behandlinger
- Cryolipolysis
- Trimflox
- Lymfemassage
- Korathelix
- Amberline Tide
Produkter
Priser
Kontakt
Clinic
Coded - Design and coding required
5+ page

```html
<!DOCTYPE html>
<html lang="da">
<head>
<meta charset="utf-8">
<title>Lirava – Body &amp; Health</title>
<link href="https://fonts.googleapis.com/css2?family=Oswald:wght@500;600&family=Poppins:wght@300;400;500;600;700&display=swap" rel="stylesheet">
<style>
:root{
  --pink:#c13d83;
  --pink-deep:#a8336f;
  --orange:#f7a13d;
  --orange-2:#f8823c;
  --green:#a7d235;
  --teal:#1eb5c1;
  --navy:#2f3a4d;
  --ink:#222;
  --muted:#8a8a8a;
  --line:#e6e6e6;
  --white:#fff;
}
*{box-sizing:border-box;margin:0;padding:0}
html,body{width:1200px;height:4082px;overflow:hidden}
body{font-family:'Poppins',sans-serif;color:var(--ink);background:var(--white)}
.section{position:relative;width:1200px}
.center{text-align:center}

/* top bar */
.topbar{height:33px;background:var(--pink);display:flex;align-items:center;justify-content:space-between;padding:0 130px;color:var(--white);font-size:11px}
.topbar .contacts{display:flex;gap:26px}
.topbar .contacts span{display:flex;align-items:center;gap:7px}
.socials{display:flex;gap:7px}
.socials i{width:18px;height:18px;border-radius:50%;background:var(--white);opacity:.9;display:block}

/* header */
.header{height:97px;display:flex;align-items:center;justify-content:space-between;padding:0 130px}
.brand{display:flex;flex-direction:column;line-height:1}
.brand .name{font-size:38px;font-weight:500;color:var(--pink)}
.brand .tag{font-size:13px;font-weight:500;color:var(--pink);margin-top:4px;letter-spacing:1px}
.nav{display:flex;gap:34px;font-size:14px;color:var(--pink)}
.nav .active{font-weight:600}

/* hero */
.hero{height:651px;background:linear-gradient(100deg,#8c7a6c 0%,#cbb7a5 30%,#eadfd4 55%,#f3a55c 78%,#e9d8c7 100%)}
.hero-box{position:absolute;left:300px;top:278px;width:712px;height:223px;background:rgba(20,18,18,.55);color:var(--white);text-align:center;padding-top:34px}
.hero-box .kicker{font-size:17px;font-weight:300}
.hero-box h1{font-size:36px;font-weight:600;margin-top:8px;white-space:nowrap}
.btns{display:flex;justify-content:center;gap:16px;margin-top:22px}
.btn{height:40px;padding:0 26px;border-radius:20px;font-size:13px;display:flex;align-items:center}
.btn.primary{background:var(--pink)}
.btn.ghost{border:1.5px solid var(--white)}

/* treatment tiles */
.tiles{height:226px;display:flex}
.tile{flex:1;color:var(--white);text-align:center;padding-top:64px}
.tile svg{width:46px;height:46px}
.tile h3{font-size:19px;font-weight:600;margin-top:10px}
.tile small{display:block;font-size:8px;margin-top:12px;letter-spacing:1px;opacity:.85}
.t1{background:var(--orange)}.t2{background:var(--orange-2)}.t3{background:var(--green)}.t4{background:var(--teal)}

.title{font-family:'Oswald',sans-serif;font-weight:600;font-size:32px;letter-spacing:.5px;text-transform:uppercase}
.lead{font-size:11.5px;color:#666;line-height:1.8;width:880px;margin:0 auto}

/* why */
.why{height:626px;padding-top:70px}
.why .lead{margin-top:14px}
.why-photo{position:absolute;left:131px;top:185px;width:936px;height:370px;background:linear-gradient(120deg,#f3ece6 0%,#d9b79c 40%,#b98a6b 65%,#2a2421 100%);box-shadow:0 2px 8px rgba(0,0,0,.25)}
.why-photo::after{content:"";position:absolute;inset:10px;border:2px solid rgba(255,255,255,.85)}

/* stories */
.stories{height:430px;padding-top:48px}
.cards{position:absolute;left:128px;top:106px;display:flex;gap:14px}
.card{width:316px;height:218px;background:var(--white);box-shadow:0 2px 12px rgba(0,0,0,.1);padding:24px 30px}
.card-head{display:flex;align-items:center;gap:18px}
.avatar{width:66px;height:66px;border-radius:50%;background:linear-gradient(135deg,#e9d5cc,#b68b76)}
.card-head h4{font-size:17px;font-weight:500}
.card-head p{font-size:9px;color:var(--green);margin-top:6px}
.card .body{font-size:11px;color:var(--muted);line-height:1.75;margin-top:18px}
.dots{position:absolute;left:0;right:0;top:374px;display:flex;justify-content:center;gap:7px}
.dots i{width:9px;height:9px;border-radius:50%;background:#d7d7d7}
.dots i:first-child{background:var(--green)}

/* team */
.team{height:421px;background:linear-gradient(110deg,#c9ad98 0%,#e8d7c9 35%,#9c7a66 60%,#2b2524 100%);color:var(--white)}
.team-shade{position:absolute;inset:0;background:rgba(0,0,0,.25)}
.team .meet{position:absolute;top:100px;width:100%;font-size:10px;letter-spacing:1px}
.team .title{position:absolute;top:124px;width:100%;font-size:28px;color:var(--white)}
.team .title em{font-style:normal;color:var(--green)}
.steps{position:absolute;left:120px;top:224px;display:flex;gap:50px}
.step{width:300px;display:flex;gap:16px}
.step .num{font-family:'Oswald',sans-serif;font-size:48px;font-weight:600;line-height:1}
.step h5{font-size:13px;font-weight:500;padding-bottom:6px;position:relative}
.step h5::after{content:"";position:absolute;left:0;bottom:0;width:40px;height:2px;background:var(--green)}
.step p{font-size:11px;line-height:1.6;margin-top:8px}

/* clients */
.clients{height:430px;padding-top:50px}
.clients .lead{margin-top:12px;width:560px;font-size:11px;line-height:1.7}
.quote-box{position:absolute;left:201px;top:168px;width:795px;height:232px;border:1px solid var(--line);box-shadow:0 2px 10px rgba(0,0,0,.08);text-align:center;padding:18px 60px}
.quote-box .mark{font-family:'Oswald',sans-serif;font-size:40px;color:var(--green);line-height:1}
.quote-box p{font-size:11px;color:#555;line-height:1.7;margin-top:4px}
.quote-box .avatar{width:48px;height:48px;margin:12px auto 0}
.quote-box h6{font-size:14px;font-weight:500;margin-top:6px}
.quote-box small{font-size:10px;color:var(--muted)}
.arrow{position:absolute;top:100px;width:30px;height:30px;border-radius:50%;border:1.5px solid var(--green);display:flex;align-items:center;justify-content:center}
.arrow.left{left:-14px;background:var(--white)}.arrow.right{right:-14px;background:var(--white)}

/* subscribe */
.subscribe{height:183px;background:linear-gradient(90deg,var(--pink),#c45a93 60%,var(--pink-deep));color:var(--white)}
.subscribe .title{position:absolute;top:46px;width:100%;font-size:24px}
.sub-form{position:absolute;left:283px;top:98px;width:634px;height:38px;background:var(--white);border-radius:19px;display:flex;align-items:center;justify-content:space-between;padding:0 0 0 20px;font-size:11px;color:#333}
.sub-form b{height:38px;padding:0 24px;display:flex;align-items:center;color:var(--pink);font-weight:500;border-left:1px solid var(--line)}

/* map */
.map{height:405px;background:linear-gradient(135deg,#e9ecde 0%,#dfe6d3 45%,#e4e9ee 100%)}
.pin{position:absolute;left:584px;top:176px}

/* contact tiles */
.contact{height:253px;display:flex}
.ct{flex:1;color:var(--white);text-align:center;padding-top:76px}
.ct h4{font-size:16px;font-weight:600;margin-top:20px}
.ct small{display:block;font-size:9px;letter-spacing:2px;margin-top:16px}
.c1{background:var(--orange-2)}.c2{background:var(--green)}.c3{background:var(--teal)}

/* footer */
.footer{height:327px;background:var(--navy);text-align:center;color:var(--white);padding-top:62px}
.footer .brand{align-items:center}
.footer .brand .name{font-size:60px}
.footer .brand .tag{font-size:20px}
.fnav{display:flex;justify-content:center;gap:22px;font-size:9px;letter-spacing:2px;margin-top:26px;opacity:.8}
.fsocial{display:flex;justify-content:center;gap:40px;margin-top:28px}
.fsocial i{width:16px;height:16px;border-radius:50%;background:var(--white);display:block}
</style>
</head>
<body>

<div class="section topbar">
  <div class="contacts">
    <span><svg width="10" height="12" viewBox="0 0 10 12"><rect x="1" y="0.5" width="8" height="11" rx="1.5" fill="none" stroke="#fff"/></svg>+45 55 01 42 29</span>
    <span><svg width="10" height="12" viewBox="0 0 10 12"><rect x="1" y="0.5" width="8" height="11" rx="1.5" fill="none" stroke="#fff"/></svg>+45 55 01 42 30</span>
    <span><svg width="12" height="9" viewBox="0 0 12 9"><rect x="0.5" y="0.5" width="11" height="8" fill="none" stroke="#fff"/><path d="M1 1l5 4 5-4" fill="none" stroke="#fff"/></svg>hello@liravaclinic.com</span>
  </div>
  <div class="socials"><i></i><i></i><i></i><i></i><i></i><i></i></div>
</div>

<header class="section header">
  <div class="brand"><span class="name">Lirava</span><span class="tag">Body &amp; Health</span></div>
  <nav class="nav"><span class="active">Lirava</span><span>Behandlinger</span><span>Produkter</span><span>Priser</span><span>Kontakt</span></nav>
</header>

<section class="section hero" role="img" aria-label="Slideshow photo of a therapist giving a cryolipolysis treatment in the clinic">
  <div class="hero-box">
    <div class="kicker">Frys fedt og cellulite væk – uden kirurgi.</div>
    <h1>Velkommen til Lirava Body &amp; Health</h1>
    <div class="btns"><span class="btn primary">Læs mere</span><span class="btn ghost">Kontakt os</span></div>
  </div>
</section>

<section class="section tiles">
  <div class="tile t1">
    <svg viewBox="0 0 46 46" fill="none" stroke="#fff" stroke-width="2"><path d="M23 4v38M6 13l34 20M6 33l34-20M18 7l5 4 5-4M18 39l5-4 5 4"/></svg>
    <h3>Cryolipolysis</h3><small>LÆS MERE</small>
  </div>
  <div class="tile t2">
    <svg viewBox="0 0 46 46" fill="none" stroke="#fff" stroke-width="2"><path d="M14 6c0 12 6 14 6 20s-6 8-6 14M32 6c0 12-6 14-6 20s6 8 6 14M18 26h10"/></svg>
    <h3>Trimflox</h3><small>LÆS MERE</small>
  </div>
  <div class="tile t3">
    <svg viewBox="0 0 46 46" fill="none" stroke="#fff" stroke-width="2"><rect x="6" y="6" width="34" height="34" rx="4"/><path d="M14 16a9 9 0 0 1 18 0z"/><path d="M23 16l3-5"/></svg>
    <h3>Lymfemassage</h3><small>LÆS MERE</small>
  </div>
  <div class="tile t4">
    <svg viewBox="0 0 46 46" fill="none" stroke="#fff" stroke-width="2"><rect x="14" y="4" width="18" height="8" rx="1"/><rect x="10" y="12" width="26" height="30" rx="3"/><path d="M23 20v14M16 27h14"/></svg>
    <h3>Korathelix</h3><small>LÆS MERE</small>
  </div>
</section>

<section class="section why center">
  <h2 class="title">Hvorfor vælge Cryolipolysis</h2>
  <p class="lead">Velkommen til Lirava Klinik. Cryolipolysis nedfryser fedtceller skånsomt, så kroppen selv nedbryder dem over de følgende uger.<br>Behandlingen er uden nåle og uden nedetid – du kan gå direkte tilbage til hverdagen med en strammere og glattere hud.</p>
  <div class="why-photo" role="img" aria-label="Photo of a cryolipolysis applicator being used on a client's abdomen"></div>
</section>

<section class="section stories center">
  <h2 class="title" style="font-size:26px">Succeshistorier</h2>
  <div class="cards" style="text-align:left">
    <div class="card">
      <div class="card-head"><div class="avatar" role="img" aria-label="Client portrait"></div><div><h4>Marta Solvani</h4><p>Tabt 12 kg på 5 måneder</p></div></div>
      <p class="body">Efter tre cryo-behandlinger kunne jeg endelig se forskel på maven. Personalet er varmt og professionelt, og klinikken er smuk…</p>
    </div>
    <div class="card">
      <div class="card-head"><div class="avatar" role="img" aria-label="Client portrait"></div><div><h4>Henrik Dallo</h4><p>Tabt 9 kg på 4 måneder</p></div></div>
      <p class="body">Over de sidste måneder har jeg langsomt arbejdet mod mit mål, og behandlingerne gav mig det sidste skub mod en stærkere krop.</p>
    </div>
    <div class="card">
      <div class="card-head"><div class="avatar" role="img" aria-label="Client portrait"></div><div><h4>Clara Westmund</h4><p>Tabt 14 kg på 6 måneder</p></div></div>
      <p class="body">Lymfemassagen og cryolipolysis har givet mig en glattere hud og mere energi. Jeg anbefaler Lirava til alle mine veninder…</p>
    </div>
  </div>
  <div class="dots"><i></i><i></i><i></i></div>
</section>

<section class="section team center" role="img" aria-label="Photo of a therapist giving a lymphatic massage to a client's leg">
  <div class="team-shade"></div>
  <div class="meet">MØD VORES TEAM</div>
  <h2 class="title">Venlige og <em>Passionerede</em></h2>
  <div class="steps" style="text-align:left">
    <div class="step"><div class="num">01</div><div><h5>KONSULTATION</h5><p>Vi lytter til dine ønsker og laver en personlig plan, der passer til din krop og dine mål.</p></div></div>
    <div class="step"><div class="num">02</div><div><h5>BEHANDLING</h5><p>Sikker og komfortabel behandling i rolige omgivelser, udført af certificerede terapeuter.</p></div></div>
    <div class="step"><div class="num">03</div><div><h5>RESULTAT</h5><p>Synlige resultater efter få uger, med opfølgning og gode råd til at holde formen.</p></div></div>
  </div>
</section>

<section class="section clients center">
  <h2 class="title" style="font-size:26px">Det siger vores kunder</h2>
  <p class="lead">Ægte oplevelser fra kvinder, der har fået en ny kropsfølelse<br>gennem vores behandlinger hos Lirava</p>
  <div class="quote-box">
    <div class="arrow left"><svg width="10" height="10" viewBox="0 0 10 10"><path d="M7 1L3 5l4 4" fill="none" stroke="#a7d235" stroke-width="1.6"/></svg></div>
    <div class="arrow right"><svg width="10" height="10" viewBox="0 0 10 10"><path d="M3 1l4 4-4 4" fill="none" stroke="#a7d235" stroke-width="1.6"/></svg></div>
    <div class="mark">&ldquo;</div>
    <p>Jeg havde prøvet alt mod cellulite på lårene, men intet virkede før jeg kom til Lirava. Behandlingen var behagelig, stemningen var rolig og smuk, og efter seks uger kunne jeg tydeligt se forskellen i spejlet.</p>
    <div class="avatar" role="img" aria-label="Client portrait"></div>
    <h6>Nadia Ferrel</h6>
    <small>Kunde siden 2022</small>
  </div>
</section>

<section class="section subscribe center">
  <h2 class="title">Tilmeld dig &amp; få gode nyheder</h2>
  <div class="sub-form"><span>Indtast din e-mail</span><b>TILMELD</b></div>
</section>

<section class="section map" role="img" aria-label="Map showing the clinic location">
  <svg class="pin" width="32" height="44" viewBox="0 0 32 44"><path d="M16 2C8 2 2 8 2 16c0 10 14 26 14 26s14-16 14-26C30 8 24 2 16 2z" fill="#c13d83"/><circle cx="16" cy="16" r="5" fill="#fff"/></svg>
</section>

<section class="section contact">
  <div class="ct c1">
    <svg width="22" height="34" viewBox="0 0 22 34" fill="none" stroke="#fff" stroke-width="2"><rect x="2" y="2" width="18" height="30" rx="3"/><path d="M9 27h4"/></svg>
    <h4>+45 55 01 47 00</h4><small>TELEFON</small>
  </div>
  <div class="ct c2">
    <svg width="26" height="34" viewBox="0 0 26 34" fill="none" stroke="#fff" stroke-width="2"><path d="M13 2C7 2 2 7 2 13c0 8 11 19 11 19s11-11 11-19C24 7 19 2 13 2z"/><circle cx="13" cy="13" r="4"/></svg>
    <h4>Nørrebro, 2200 København, Danmark</h4><small>ADRESSE</small>
  </div>
  <div class="ct c3">
    <svg width="32" height="34" viewBox="0 0 32 34" fill="none" stroke="#fff" stroke-width="2"><rect x="2" y="8" width="28" height="20" rx="2"/><path d="M2 10l14 10 14-10"/></svg>
    <h4>care@liravaclinic.com</h4><small>E-MAIL</small>
  </div>
</section>

<footer class="section footer">
  <div class="brand"><span class="name">Lirava</span><span class="tag">Body &amp; Health</span></div>
  <div class="fnav"><span>LIRAVA</span><span>BEHANDLINGER</span><span>PRODUKTER</span><span>PRISER</span><span>KONTAKT</span></div>
  <div class="fsocial"><i></i><i></i><i></i><i></i><i></i></div>
</footer>

</body>
</html>
```